Business Card for Coastal Tundrabridge Advisory

We need a business card for Coastal Tundrabridge Advisory. The company website address is provided below. The company logo is attached. We provide specialized permafrost services to the mining, transportation, and oil & gas industries. The card should be prepared for:
Matthias Korhonen, PhD.
Coastal Tundrabridge Advisory
PO Box 418259
Quillwater, Alaska 99642
Direct: +1-907-555-0143
Email: mkorhonen@tundrabridgeadvisory.example
Website: www.coastaltundrabridgeadvisory.example

```html
<!DOCTYPE html>
<html lang="en">
<head>
<meta charset="utf-8">
<title>Coastal Tundrabridge Advisory — Business Card</title>
<link rel="stylesheet" href="https://fonts.googleapis.com/css2?family=Roboto:ital,wght@0,300;0,400;0,700;1,400&family=Roboto+Condensed:ital,wght@0,700;1,400&display=swap">
<style>
  :root {
    --backdrop: #232323;
    --card-light: #ebeae8;
    --card-dark: #0e1620;
    --ink: #15191f;
    --ink-soft: #2a2e34;
    --paper-text: #e9ecef;
  }
  * { margin: 0; padding: 0; box-sizing: border-box; }
  html, body {
    width: 1200px; height: 780px; overflow: hidden;
    background: var(--backdrop);
    font-family: "Roboto", sans-serif;
  }
  .stage {
    width: 1200px; height: 780px;
    display: flex; align-items: center; justify-content: center; gap: 40px;
  }
  .card {
    position: relative;
    width: 540px; height: 309px;
    border-radius: 24px;
    overflow: hidden;
    box-shadow: 0 14px 30px rgba(0,0,0,.45);
  }
  /* Front */
  .card-front { background: var(--card-light); color: var(--ink); }
  .person { position: absolute; left: 14px; top: 80px; width: 212px; text-align: right; }
  .person-name { font-size: 24px; line-height: 1.05; white-space: nowrap; }
  .person-first { font-weight: 700; letter-spacing: -0.3px; }
  .person-last { font-weight: 300; }
  .person-title { font-size: 14px; font-weight: 700; margin-top: 2px; }
  .address {
    position: absolute; left: 40px; top: 196px;
    font-style: normal;
    font-size: 13.5px; line-height: 1.45; color: var(--ink-soft);
  }
  .divider {
    position: absolute; left: 240px; top: 92px;
    width: 1.5px; height: 112px; background: var(--ink);
  }
  .contacts {
    position: absolute; left: 254px; top: 120px;
    list-style: none; font-size: 11.5px; color: var(--ink-soft);
  }
  .contacts li { display: flex; align-items: center; gap: 6px; line-height: 1.6; white-space: nowrap; }
  .contacts svg { width: 11px; height: 11px; flex: none; fill: var(--ink); }
  /* Back */
  .card-back { background: var(--card-dark); color: var(--paper-text); text-align: center; }
  .company-name {
    position: absolute; left: 0; right: 0; top: 96px;
    font-family: "Roboto Condensed", sans-serif; font-weight: 700;
    font-size: 30px; letter-spacing: 1.5px; text-transform: uppercase; line-height: 1.15;
  }
  .services-heading {
    position: absolute; left: 0; right: 0; top: 218px;
    font-family: "Roboto Condensed", sans-serif; font-weight: 700;
    font-size: 11px; letter-spacing: .4px;
  }
  .services-text {
    position: absolute; left: 20px; right: 20px; top: 238px;
    font-family: "Roboto Condensed", sans-serif; font-style: italic; font-weight: 400;
    font-size: 11.5px; color: #cfd4da;
  }
</style>
</head>
<body>
<main class="stage">
  <section class="card card-front" aria-label="Business card front">
    <div class="person">
      <h1 class="person-name"><span class="person-first">Matthias</span> <span class="person-last">Korhonen</span></h1>
      <p class="person-title">PhD</p>
    </div>
    <address class="address">PO Box 418259<br>Quillwater, Alaska 99642</address>
    <div class="divider"></div>
    <ul class="contacts">
      <li>
        <svg viewBox="0 0 24 24" aria-hidden="true"><path d="M6.6 10.8a15 15 0 0 0 6.6 6.6l2.2-2.2a1 1 0 0 1 1-.25 11.4 11.4 0 0 0 3.6.57 1 1 0 0 1 1 1V20a1 1 0 0 1-1 1A17 17 0 0 1 3 4a1 1 0 0 1 1-1h3.5a1 1 0 0 1 1 1c0 1.250.2 2.450.57 3.57a1 1 0 0 1-.25 1z"/></svg>
        +1-907-555-0143
      </li>
      <li>
        <svg viewBox="0 0 24 24" aria-hidden="true"><path d="M3 5h18a1 1 0 0 1 1 1v12a1 1 0 0 1-1 1H3a1 1 0 0 1-1-1V6a1 1 0 0 1 1-1zm9 7.5L20 7H4z"/></svg>
        mkorhonen@tundrabridgeadvisory.example
      </li>
      <li>
        <svg viewBox="0 0 24 24" aria-hidden="true"><path d="M12 2a10 10 0 1 0 0 20 10 10 0 0 0 0-20zm6.9 6h-2.9a15 15 0 0 0-1.4-3.6A8 8 0 0 1 18.9 8zM12 4a13 13 0 0 1 1.9 4h-3.8A13 13 0 0 1 12 4zM4.3 14a8 8 0 0 1 0-4h3.3a16 16 0 0 0 0 4zm.8 2h2.9a15 15 0 0 0 1.4 3.6A8 8 0 0 1 5.1 16zM8 8H5.1a8 8 0 0 1 4.3-3.6A15 15 0 0 0 8 8zm4 12a13 13 0 0 1-1.9-4h3.8A13 13 0 0 1 12 20zm2.3-6H9.7a14 14 0 0 1 0-4h4.6a14 14 0 0 1 0 4zm.3 5.6a15 15 0 0 0 1.4-3.6h2.9a8 8 0 0 1-4.3 3.6zm1.8-5.6a16 16 0 0 0 0-4h3.3a8 8 0 0 1 0 4z"/></svg>
        www.coastaltundrabridgeadvisory.example
      </li>
    </ul>
  </section>

  <section class="card card-back" aria-label="Business card back">
    <h2 class="company-name">Coastal Tundrabridge<br>Advisory</h2>
    <p class="services-heading">OUR SERVICES</p>
    <p class="services-text">We provide specialized permafrost services to the mining, transportation, and oil &amp; gas industries</p>
  </section>
</main>
</body>
</html>
```